Harbourline Electrical Solutions

On one side. LOGO (underneath:) Commercial Industrial Residential

- NAME & CONTACT DETAILS

Marcus T. Hollings
Project Manager

(Cell icon) (441) 555-0187
(Email icon) hlelectricalsolutions@mailvento.com
(Facebook & Instagram icons )@hlelectricalsolutions

Other side: LOGO - underneath ELECTRICAL CONSTRUCTION & MAINTENANCE . LED LIGHTING & AUTOMATION . LIFE SAFETY SYSTEMS (FIRE ALARM / SECURITY) . DATA & COMMUNICATION

```html
<!DOCTYPE html>
<html lang="en">
<head>
<meta charset="utf-8">
<title>Harbourline Electrical Solutions – Business Card</title>
<link href="https://fonts.googleapis.com/css2?family=Montserrat:wght@300;400;500;600;700&display=swap" rel="stylesheet">
<style>
  :root {
    --backdrop: #2b2b2d;
    --card-grey: #505050;
    --brand-teal: #10566d;
    --brand-teal-deep: #0d4a5e;
    --ink: #3c3c3c;
    --paper: #ffffff;
  }
  * { margin: 0; padding: 0; box-sizing: border-box; }
  html, body {
    width: 1200px; height: 1200px; overflow: hidden;
    background: var(--backdrop);
    font-family: "Montserrat", Arial, sans-serif;
  }
  .stage { position: relative; width: 1200px; height: 1200px; }

  .card {
    position: absolute; left: 294px; width: 612px; height: 366px; overflow: hidden;
  }

  /* Services side */
  .card--services { top: 216px; background: var(--card-grey); }
  .service-list {
    position: absolute; left: 82px; top: 138px; list-style: none;
    color: #fff; font-weight: 500; font-size: 12.5px; line-height: 14.5px;
  }
  .service-list li { position: relative; padding-left: 9px; margin-bottom: 8px; }
  .service-list li::before {
    content: ""; position: absolute; left: 0; top: 4px;
    width: 4.5px; height: 4.5px; background: #fff;
  }
  .brand-band {
    position: absolute; left: 442px; top: 0; width: 170px; height: 366px;
    background: var(--brand-teal);
  }
  .brand-band__name {
    position: absolute; left: 45px; top: 330px;
    transform: rotate(-90deg); transform-origin: 0 0;
    color: var(--brand-teal-deep); font-weight: 400;
    font-size: 17px; line-height: 19px; letter-spacing: 3px; white-space: nowrap;
  }

  /* Contact side */
  .card--contact { top: 630px; background: var(--paper); }
  .brand-name {
    position: absolute; left: 47px; top: 34px;
    color: var(--brand-teal); font-weight: 500;
    font-size: 21px; line-height: 24px; letter-spacing: 3px;
  }
  .sectors {
    position: absolute; left: 46px; top: 112px;
    font-size: 10px; font-weight: 500; letter-spacing: 2.6px; color: #222;
  }
  .sectors .sep { color: var(--brand-teal); margin: 0 5px; }
  .person { position: absolute; left: 46px; top: 244px; }
  .person__name { color: var(--brand-teal); font-weight: 700; font-size: 17px; line-height: 20px; }
  .person__role { color: var(--ink); font-weight: 500; font-size: 11.5px; line-height: 14px; }
  .person__rule { width: 49px; height: 2px; background: var(--brand-teal); margin-top: 10px; }
  .contact-line {
    position: absolute; display: flex; align-items: center; gap: 4px;
    color: var(--ink); font-weight: 300; font-size: 13px;
  }
  .contact-line svg { width: 13px; height: 13px; flex: none; }
  .contact-line--phone { left: 45px; top: 300px; }
  .contact-line--email { left: 45px; top: 319px; }
  .contact-line--social { left: 377px; top: 319px; gap: 5px; }
  .social-dot {
    width: 12px; height: 12px; border: 1px solid var(--brand-teal); border-radius: 50%;
  }
</style>
</head>
<body>
<main class="stage">

  <section class="card card--services" aria-label="Services side">
    <ul class="service-list">
      <li>ELECTRICAL CONSTRUCTION<br>&amp; MAINTENANCE</li>
      <li>LED LIGHTING &amp; AUTOMATION</li>
      <li>LIFE SAFETY SYSTEMS<br>(FIRE ALARM / SECURITY)</li>
      <li>DATA &amp; COMMUNICATION</li>
    </ul>
    <div class="brand-band">
      <div class="brand-band__name">HARBOURLINE<br>ELECTRICAL<br>SOLUTIONS</div>
    </div>
  </section>

  <section class="card card--contact" aria-label="Contact side">
    <div class="brand-name">HARBOURLINE<br>ELECTRICAL<br>SOLUTIONS</div>
    <div class="sectors">COMMERCIAL<span class="sep">|</span>INDUSTRIAL<span class="sep">|</span>RESIDENTIAL</div>

    <div class="person">
      <div class="person__name">MARCUS T. HOLLINGS</div>
      <div class="person__role">Project Manager</div>
      <div class="person__rule"></div>
    </div>

    <div class="contact-line contact-line--phone">
      <svg viewBox="0 0 14 14" aria-hidden="true">
        <circle cx="7" cy="7" r="6.3" fill="none" stroke="#10566d" stroke-width="1"/>
        <path d="M4.6 3.8c.4-.3.8-.2 1 .2l.5 1c.1.3 0 .5-.2.7l-.3.3c.4.8 1 1.4 1.8 1.8l.3-.3c.2-.2.4-.3.7-.2l1 .5c.4.2.5.6.2 1-.6.8-1.4.9-2.4.4C5.9 8.5 5 7.6 4.4 6.3c-.4-1-.4-1.9.2-2.5z" fill="#10566d"/>
      </svg>
      (441) 555-0187
    </div>
    <div class="contact-line contact-line--email">
      <svg viewBox="0 0 14 14" aria-hidden="true">
        <circle cx="7" cy="7" r="6.3" fill="none" stroke="#10566d" stroke-width="1"/>
        <rect x="3.8" y="4.8" width="6.4" height="4.4" fill="none" stroke="#10566d" stroke-width="0.9"/>
        <path d="M3.8 4.8 7 7.3l3.2-2.5" fill="none" stroke="#10566d" stroke-width="0.9"/>
      </svg>
      hlelectricalsolutions@mailvento.com
    </div>
    <div class="contact-line contact-line--social">
      <span class="social-dot" aria-hidden="true"></span>
      <span class="social-dot" aria-hidden="true"></span>
      @hlelectricalsolutions
    </div>
  </section>

</main>
</body>
</html>
```